Vantor Wear and Fuel is looking for a Clothing/Supplement Online Store Website!

Must be convenient, and user friendly, with vibrant colors that catch the eye!

Target Market(s)

Athletes, and Fashion Customers

Industry/Entity Type

Fitness

Coding

Coded - Design and coding required

Number of Pages Required

3 page

Font styles to use
Decorative

Colors

Designer to choose colors to be used in the design.

Requirements
Must have
• Somewhere to feature products, features to promote discounts and make announcements.
Nice to have
• My logos on each page

```html
<!DOCTYPE html>
<html lang="en">
<head>
<meta charset="utf-8">
<title>Vantor Wear and Fuel</title>
<link href="https://fonts.googleapis.com/css2?family=Raleway:wght@400;500;600;700&family=Montserrat:wght@500;700&display=swap" rel="stylesheet">
<style>
:root{
  --ink:#1d1d1f;
  --dark:#2b2a2d;
  --footer:#403e42;
  --grey-bg:#f4f3f5;
  --line:#dcdcdc;
  --muted:#888;
  --sale:#e2262b;
  --btn:#3a393c;
  --white:#fff;
}
*{box-sizing:border-box;margin:0;padding:0}
html,body{width:1200px;height:3966px;overflow:hidden}
body{position:relative;font-family:"Raleway",sans-serif;color:var(--ink);background:var(--white)}
.abs{position:absolute}
.topbar{left:0;top:0;width:1200px;height:37px;background:var(--dark);color:#ddd;font-size:12px}
.topbar .contact{left:145px;top:11px}
.topbar .account{right:150px;top:11px}
.cart-badge{display:inline-block;width:14px;height:14px;border-radius:50%;background:var(--white);color:var(--dark);font-size:9px;text-align:center;line-height:14px;margin-left:6px}
.header{left:0;top:37px;width:1200px;height:99px;background:var(--white)}
.brand{font-family:"Montserrat",sans-serif;font-weight:700;letter-spacing:1px}
.header .brand{left:145px;top:34px;font-size:28px;color:#555;display:flex;align-items:center;gap:8px}
.mark{width:14px;height:14px;background:#555;border-radius:50%;display:inline-block}
.nav{left:379px;top:40px;display:flex;gap:23px;font-size:14px;font-weight:600}
.nav .active{position:relative}
.nav .active::after{content:"";position:absolute;left:0;right:0;bottom:-42px;height:2px;background:var(--ink)}
.search{left:1028px;top:36px;width:27px;height:27px;border-radius:50%;background:var(--dark)}
.hero{left:0;top:136px;width:1200px;height:562px;background:linear-gradient(90deg,#8f8f93 0%,#b9b9bc 40%,#cfcfd1 70%,#bdbdbf 100%)}
.hero-title{left:708px;top:283px;font-family:"Montserrat",sans-serif;font-weight:700;font-size:58px;line-height:66px;color:#3a393c;letter-spacing:1px}
.btn{background:var(--btn);color:var(--white);font-weight:700;text-transform:uppercase;text-align:center}
.hero .buy{left:708px;top:368px;width:128px;height:38px;line-height:38px;font-size:13px}
.arrow{width:42px;height:42px;border-radius:50%;background:#1a1a1a}
.dots{left:566px;top:518px;display:flex;gap:4px}
.dots span{width:10px;height:10px;border-radius:50%;background:#eee;border:1px solid #999}
.tile{top:715px;height:255px;color:var(--white)}
.tile .label{position:absolute;left:0;right:0;bottom:22px;text-align:center;font-weight:700;font-size:30px;line-height:34px}
.section-title{left:0;width:1200px;text-align:center;font-size:36px;font-weight:600}
.card{width:211px;height:269px;border:1px solid var(--line);background:var(--white);text-align:center}
.card .pic{margin:10px auto 0;width:150px;height:150px}
.card .name{margin-top:13px;font-weight:700;font-size:15px}
.price{margin-top:8px;font-size:12px}
.price s{color:var(--muted);margin-right:8px}
.price b{color:var(--sale);font-weight:500}
.card .add{margin:12px auto 0;width:84px;height:20px;line-height:20px;font-size:8px}
.round{width:34px;height:34px;border-radius:50%;border:1px solid #bbb;background:var(--white)}
.promo-box{background:var(--white);padding:30px 27px}
.promo-box h3{font-size:32px;font-weight:500;line-height:36px}
.promo-box p{margin-top:16px;font-size:14px;color:#555}
.promo-box p b{font-size:19px;font-weight:600;color:var(--ink)}
.promo-box .btn{margin-top:18px;width:99px;height:28px;line-height:28px;font-size:11px}
.news-bg{left:0;top:2184px;width:1200px;height:737px;background:var(--grey-bg)}
.post{top:2430px;width:288px;height:407px;background:var(--white);box-shadow:0 0 6px rgba(0,0,0,.08)}
.post .pic{margin:5px 5px 0;height:171px}
.post .meta{margin:20px 17px 0;display:flex;justify-content:space-between;font-size:12px;color:#777}
.post .meta b{color:var(--sale);font-weight:500}
.post h4{margin:18px 17px 0;font-size:17px;font-weight:700}
.post h4 span{font-weight:400;color:#555}
.post p{margin:12px 17px 0;font-size:11.5px;line-height:21px;color:#999}
.post .actions{margin:16px 17px 0;display:flex;gap:8px}
.share{width:34px;height:32px;background:var(--btn)}
.more{height:32px;line-height:30px;padding:0 12px;border:1px solid #555;font-size:13px;font-weight:600}
.news-title{top:2358px}
.newsletter h2{left:0;width:1200px;top:3008px;text-align:center;font-size:36px;font-weight:700}
.newsletter .sub{left:0;width:1200px;top:3070px;text-align:center;font-size:14px;color:#555}
.input{left:296px;top:3123px;width:477px;height:48px;box-shadow:0 0 8px rgba(0,0,0,.12);font-size:12px;color:#666;padding:16px 17px}
.signup{left:782px;top:3123px;width:122px;height:48px;line-height:48px;font-size:16px;background:var(--btn)}
.feature{top:3237px;width:286px;height:166px;border:1px solid var(--line);text-align:center}
.feature svg{margin-top:20px}
.feature h5{margin-top:10px;font-size:17px;font-weight:700}
.feature p{margin-top:10px;font-size:13px;line-height:20px;color:#888}
.footer{left:0;top:3442px;width:1200px;height:524px;background:var(--footer);color:var(--white)}
.footer .brand{left:0;width:1200px;top:174px;text-align:center;font-size:40px}
.follow{left:0;width:1200px;top:254px;text-align:center;font-size:34px;font-weight:500}
.social{width:42px;height:42px;border-radius:50%;background:var(--white);top:321px}
.paycard{top:332px;width:37px;height:24px;border-radius:2px}
.foot-nav{left:0;width:1200px;top:435px;text-align:center;font-size:16px;font-weight:500;word-spacing:4px}
.copy{left:0;width:1200px;top:479px;text-align:center;font-size:11px}
</style>
</head>
<body>

<div class="abs topbar">
  <div class="abs contact">&#9742; Call us : 1 800 555 0142 &nbsp;|&nbsp; &#9993; Email : info@vantorwearandfuel.com</div>
  <div class="abs account">Log In &nbsp;|&nbsp; Register &nbsp;&nbsp; &#128722;<span class="cart-badge">0</span></div>
</div>

<header class="abs header">
  <div class="abs brand"><span class="mark"></span>VANTOR</div>
  <nav class="abs nav">
    <span class="active">HOME</span><span>ABOUT</span><span>PRODUCTS</span><span>CLOTHING</span><span>ONLINE STORE</span><span>FEATURES</span><span>CONTACT</span>
  </nav>
  <div class="abs search">
    <svg width="27" height="27" viewBox="0 0 27 27"><circle cx="12" cy="12" r="5" fill="none" stroke="#fff" stroke-width="2"/><line x1="16" y1="16" x2="19" y2="19" stroke="#fff" stroke-width="2"/></svg>
  </div>
</header>

<section class="abs hero" role="img" aria-label="Bearded man in cap, sunglasses and denim jacket against a weathered grey wall">
  <div class="abs arrow" style="left:51px;top:204px"><svg width="42" height="42"><polyline points="24,14 17,21 24,28" fill="none" stroke="#fff" stroke-width="2.5"/></svg></div>
  <div class="abs arrow" style="left:1106px;top:204px"><svg width="42" height="42"><polyline points="18,14 25,21 18,28" fill="none" stroke="#fff" stroke-width="2.5"/></svg></div>
  <div class="abs dots"><span></span><span></span><span></span><span></span><span></span></div>
</section>
<h1 class="abs hero-title">VANTOR<br>WEAR &amp;<br>FUEL</h1>
<div class="abs btn" style="left:708px;top:504px;width:128px;height:38px;line-height:38px;font-size:13px">Buy Now</div>

<div class="abs tile" style="left:14px;width:382px;background:linear-gradient(135deg,#4a4d55,#8d3a5a 60,#c23a6e);background:linear-gradient(135deg,#4a4d55 0%,#6a4555 55%,#c7386e 100%)" role="img" aria-label="Sports bra, leggings and trainers laid flat"><div class="label">APPAREL</div></div>
<div class="abs tile" style="left:410px;width:380px;background:linear-gradient(135deg,#3a3733,#5f5a52 60%,#a0806a)" role="img" aria-label="Supplement tubs, shaker and kettlebell"><div class="label">NUTRITION<br>SUPPLEMENTS</div></div>
<div class="abs tile" style="left:804px;width:382px;background:linear-gradient(135deg,#6f6f70,#8a8480 55%,#c06a35)" role="img" aria-label="Woman stretching outdoors in an orange jacket"><div class="label">AT VERO EOSET</div></div>

<h2 class="abs section-title" style="top:1036px">FEATURED PRODUCTS</h2>
<div class="abs round" style="left:88px;top:1237px"><svg width="34" height="34"><polyline points="19,12 14,17 19,22" fill="none" stroke="#333" stroke-width="1.5"/></svg></div>
<div class="abs round" style="left:1075px;top:1237px"><svg width="34" height="34"><polyline points="15,12 20,17 15,22" fill="none" stroke="#333" stroke-width="1.5"/></svg></div>

<div class="abs card" style="left:143px;top:1120px"><div class="pic" style="background:linear-gradient(#7d7d80,#5a5a5d)" role="img" aria-label="Grey hoodie"></div><div class="name">PRODUCT NAME</div><div class="price"><s>$ 56.00</s><b>$46.00</b></div><div class="btn add">Add to Cart</div></div>
<div class="abs card" style="left:377px;top:1120px"><div class="pic" style="background:linear-gradient(#2a2a2a,#111)" role="img" aria-label="Black supplement tub"></div><div class="name">PRODUCT NAME</div><div class="price"><s>$ 56.00</s><b>$46.00</b></div><div class="btn add">Add to Cart</div></div>
<div class="abs card" style="left:611px;top:1120px"><div class="pic" style="background:linear-gradient(#1b1b1b,#333)" role="img" aria-label="Black cap"></div><div class="name">PRODUCT NAME</div><div class="price"><s>$ 56.00</s><b>$46.00</b></div><div class="btn add">Add to Cart</div></div>
<div class="abs card" style="left:845px;top:1120px"><div class="pic" style="background:linear-gradient(#5c5f66,#3e4046)" role="img" aria-label="Grey tank top"></div><div class="name">PRODUCT NAME</div><div class="price"><s>$ 56.00</s><b>$46.00</b></div><div class="btn add">Add to Cart</div></div>

<div class="abs" style="left:143px;top:1466px;width:510px;height:243px;background:linear-gradient(90deg,#8e8e90,#b5b5b7)" role="img" aria-label="Smiling woman in white T-shirt"></div>
<div class="abs promo-box" style="left:427px;top:1481px;width:212px;height:213px"><h3>APPAREL<br>DISCOUNT</h3><p>GET UPTO <b>20%</b> OFF</p><div class="btn">Buy Now</div></div>
<div class="abs" style="left:673px;top:1466px;width:382px;height:243px;background:linear-gradient(90deg,#7a2f33,#5a5e3a 40%,#c6c2bd)" role="img" aria-label="Green smoothie and runner tying red trainers"></div>
<div class="abs promo-box" style="left:831px;top:1481px;width:212px;height:213px;padding-left:25px"><h3>NUTRITION<br>DISCOUNT</h3><p>GET UPTO <b>30%</b> OFF</p><div class="btn">Buy Now</div></div>

<h2 class="abs section-title" style="top:1776px">WHAT’S NEW</h2>
<div class="abs round" style="left:88px;top:1977px"><svg width="34" height="34"><polyline points="19,12 14,17 19,22" fill="none" stroke="#333" stroke-width="1.5"/></svg></div>
<div class="abs round" style="left:1075px;top:1977px"><svg width="34" height="34"><polyline points="15,12 20,17 15,22" fill="none" stroke="#333" stroke-width="1.5"/></svg></div>

<div class="abs card" style="left:143px;top:1860px"><div class="pic" style="background:linear-gradient(#1e6b2b,#d8b57a)" role="img" aria-label="Capsules spilling from a green bottle"></div><div class="name">PRODUCT NAME</div><div class="price"><s>$ 56.00</s><b>$46.00</b></div><div class="btn add">Add to Cart</div></div>
<div class="abs card" style="left:377px;top:1860px"><div class="pic" style="background:linear-gradient(#7aa6c8,#5a88ad)" role="img" aria-label="Light blue hoodie"></div><div class="name">PRODUCT NAME</div><div class="price"><s>$ 56.00</s><b>$46.00</b></div><div class="btn add">Add to Cart</div></div>
<div class="abs card" style="left:611px;top:1860px"><div class="pic" style="background:linear-gradient(#222,#3a3a3a 70%,#b6d32a)" role="img" aria-label="Supplement tub, dumbbells and shaker"></div><div class="name">PRODUCT NAME</div><div class="price"><s>$ 56.00</s><b>$46.00</b></div><div class="btn add">Add to Cart</div></div>
<div class="abs card" style="left:845px;top:1860px"><div class="pic" style="background:linear-gradient(#2a2a2a,#111)" role="img" aria-label="Black polo shirt"></div><div class="name">PRODUCT NAME</div><div class="price"><s>$ 56.00</s><b>$46.00</b></div><div class="btn add">Add to Cart</div></div>

<div class="abs news-bg"></div>
<svg class="abs" style="left:0;top:2184px" width="1200" height="130" viewBox="0 0 1200 130">
  <polygon points="0,0 1200,0 1200,28 1047,30 353,126 92,32 0,32" fill="#fff"/>
  <polyline points="92,32 353,126 1047,30" fill="none" stroke="#3a393c" stroke-width="6"/>
</svg>
<h2 class="abs section-title news-title">NEWS &amp; POSTS</h2>

<article class="abs post" style="left:145px"><div class="pic" style="background:linear-gradient(90deg,#d9d4cf,#eef0f2)" role="img" aria-label="Woman holding a glass of water in a bright room"></div><div class="meta"><span>By Admin</span><b>&#9829; 1</b></div><h4>22 OCT : <span>SED UT RSPICIATIS</span></h4><p>Lorem Ipsum. Proin gravida nibh vel velit auctor aliquet. Aenean sollicitudin, lorem quis bibendum auctor, nisi elit consequat ipsum, nec sagittis sem nibh id elit.</p><div class="actions"><div class="share"></div><div class="more">READ MORE</div></div></article>
<article class="abs post" style="left:456px"><div class="pic" style="background:linear-gradient(90deg,#7a1416,#2a2a2a 60%,#5a1a1a)" role="img" aria-label="Athlete holding a shaker in a gym"></div><div class="meta"><span>By Admin</span><b>&#9829; 1</b></div><h4>22 OCT : <span>SED UT RSPICIATIS</span></h4><p>Lorem Ipsum. Proin gravida nibh vel velit auctor aliquet. Aenean sollicitudin, lorem quis bibendum auctor, nisi elit consequat ipsum, nec sagittis sem nibh id elit.</p><div class="actions"><div class="share"></div><div class="more">READ MORE</div></div></article>
<article class="abs post" style="left:767px"><div class="pic" style="background:linear-gradient(90deg,#3d3f44,#9a9ca0 60%,#2a2a2c)" role="img" aria-label="Dumbbells beside supplement tubs"></div><div class="meta"><span>By Admin</span><b>&#9829; 1</b></div><h4>22 OCT : <span>SED UT RSPICIATIS</span></h4><p>Lorem Ipsum. Proin gravida nibh vel velit auctor aliquet. Aenean sollicitudin, lorem quis bibendum auctor, nisi elit consequat ipsum, nec sagittis sem nibh id elit.</p><div class="actions"><div class="share"></div><div class="more">READ MORE</div></div></article>

<section class="newsletter">
  <div class="abs" style="left:590px;top:2976px;width:20px;height:20px;border-radius:50%;background:#444"></div>
  <h2 class="abs">SIGN UP NEWSLETTER</h2>
  <p class="abs sub">Sed ut perspiciatis unde omnis iste natus error sit voluptatem</p>
  <div class="abs input">Enter Email Address..</div>
  <div class="abs btn signup">SIGN UP</div>
  <div class="abs" style="left:909px;top:2980px;width:291px;height:162px;background:radial-gradient(ellipse at 55% 50%,#e2a91c 0%,#f2d37a 40%,#fff 72%)" role="img" aria-label="Golden softgel capsules"></div>
</section>

<div class="abs feature" style="left:143px"><svg width="40" height="36" viewBox="0 0 40 36"><path d="M8 24 V18 a12 12 0 0 1 24 0 V24" fill="none" stroke="#222" stroke-width="4"/><rect x="5" y="20" width="7" height="11" rx="2" fill="#222"/><rect x="28" y="20" width="7" height="11" rx="2" fill="#222"/></svg><h5>CUSTOMER CARE</h5><p>At vero eos et accusamus et iusto<br>dignissimos ducimblanditii</p></div>
<div class="abs feature" style="left:457px"><svg width="40" height="36" viewBox="0 0 40 36"><rect x="4" y="2" width="15" height="14" rx="2" fill="#222"/><rect x="21" y="2" width="15" height="14" rx="2" fill="#222"/><rect x="4" y="19" width="15" height="14" rx="2" fill="#222"/><rect x="21" y="19" width="15" height="14" rx="2" fill="#222"/></svg><h5>PREMIUM PACKAGING</h5><p>At vero eos et accusamus et iusto<br>dignissimos ducimblanditii</p></div>
<div class="abs feature" style="left:770px"><svg width="40" height="38" viewBox="0 0 40 38"><path d="M6 17 H12 V35 H6 Z M14 17 L21 4 C25 4 25 8 24 13 H33 C36 13 37 16 36 18 L33 32 C32 34 31 35 29 35 H14 Z" fill="none" stroke="#222" stroke-width="3" stroke-linejoin="round"/></svg><h5>SUPERIOR QUALITY</h5><p>At vero eos et accusamus et iusto<br>dignissimos ducimblanditii</p></div>

<footer class="abs footer">
  <svg class="abs" style="left:0;top:0" width="1200" height="140" viewBox="0 0 1200 140">
    <polygon points="0,0 1200,0 1200,22 353,126 0,40" fill="#fff"/>
    <polyline points="0,52 353,136 1200,34" fill="none" stroke="#fff" stroke-width="2"/>
  </svg>
  <div class="abs brand">VANTOR</div>
  <div class="abs follow">FOLLOW US TO GET A DISCOUNT</div>
  <div class="abs social" style="left:365px"></div>
  <div class="abs social" style="left:415px"></div>
  <div class="abs social" style="left:466px"></div>
  <div class="abs social" style="left:515px"></div>
  <div class="abs paycard" style="left:599px;background:#f2f2f2"></div>
  <div class="abs paycard" style="left:648px;background:#f6c343"></div>
  <div class="abs paycard" style="left:697px;background:#e9e9e9"></div>
  <div class="abs paycard" style="left:746px;background:#2c7ac6"></div>
  <div class="abs paycard" style="left:795px;background:#2a2d6e"></div>
  <nav class="abs foot-nav">HOME &nbsp;/&nbsp; ABOUT &nbsp;/&nbsp; PRODUCTS &nbsp;/&nbsp; CLOTHING &nbsp;/&nbsp; ONLINE STORE &nbsp;/&nbsp; FEATURES &nbsp;/&nbsp; CONTACT</nav>
  <div class="abs copy">Copyright ©2019 Vantor Wear and Fuel.All rights reserved</div>
</footer>

</body>
</html>
```